Pharmacy ad

need 2 pharmacy ads for the phone book. one for Brookvale Pharmacy and one for Cedarline Care Pharmacy. Dimensions for ad is 4.75in x 4.667 in. please see attached examples of ad uploaded as well logos of each pharmacy

```html
<!DOCTYPE html>
<html lang="en">
<head>
<meta charset="utf-8">
<title>Cedarline Care Pharmacy – Directory Ad</title>
<link rel="stylesheet" href="https://fonts.googleapis.com/css2?family=Montserrat:wght@400;500;600;700;800;900&family=Exo+2:ital,wght@1,600&display=swap">
<style>
  :root {
    --brand-blue: #3a4fa3;
    --brand-green: #6dbe45;
    --white: #ffffff;
    --photo-light: #e8edf1;
    --photo-mid: #c9d3da;
    --page-bg: #ffffff;
  }
  * { box-sizing: border-box; margin: 0; padding: 0; }
  html, body { width: 1200px; height: 1200px; overflow: hidden; background: var(--page-bg); }
  body { font-family: "Montserrat", sans-serif; color: var(--brand-blue); }
  .ad { position: relative; width: 1200px; height: 1200px; background: var(--white); overflow: hidden; }

  .brand-mark { position: absolute; left: 80px; top: 95px; width: 110px; height: 110px; border-radius: 50%; background: var(--brand-green); }
  .brand-text { position: absolute; left: 318px; top: 100px; display: flex; flex-direction: column; align-items: center; }
  .brand-name { font-size: 64px; font-weight: 600; letter-spacing: -1px; line-height: 1; color: var(--brand-blue); white-space: nowrap; }
  .brand-sub { display: flex; align-items: center; gap: 14px; margin-top: 8px; font-size: 42px; font-weight: 600; line-height: 1; }
  .brand-sub::before, .brand-sub::after { content: ""; width: 100px; height: 3px; background: var(--brand-green); }

  .hours { position: absolute; right: 65px; top: 80px; text-align: right; line-height: 1.24; }
  .hours-title { font-size: 26px; font-weight: 800; }
  .hours-line { font-size: 30px; font-weight: 600; }

  .tagline { position: absolute; right: 65px; top: 258px; font-family: "Exo 2", sans-serif; font-style: italic; font-weight: 600; font-size: 36px; color: var(--brand-green); }

  .photo { position: absolute; left: 0; top: 263px; width: 640px; height: 456px; background: linear-gradient(120deg, var(--photo-light) 0%, var(--photo-mid) 60%, #a9c6cf 100%); }
  .feature-panel { position: absolute; left: 0; top: 0; }

  .features { position: absolute; left: 640px; top: 347px; list-style: none; }
  .features li { position: relative; padding-left: 40px; color: var(--white); font-size: 28px; font-weight: 600; line-height: 36px; margin-bottom: 10px; }
  .features svg { position: absolute; left: 0; top: 4px; }

  .offer-band { position: absolute; left: 0; top: 718px; width: 1200px; height: 202px; background: var(--brand-green); }
  .offer { position: absolute; top: 13px; height: 175px; background: var(--white); border-radius: 0 0 34px 0; }
  .offer-senior { left: 65px; width: 517px; }
  .offer-student { left: 616px; width: 517px; }
  .offer-value { position: absolute; font-size: 136px; font-weight: 800; letter-spacing: -6px; line-height: 1; color: var(--brand-blue); }
  .offer-label { position: absolute; font-size: 34px; font-weight: 800; line-height: 38px; letter-spacing: -0.5px; }
  .offer-note { position: absolute; left: 157px; top: 142px; font-size: 23px; font-weight: 400; }

  .services { position: absolute; left: 0; top: 920px; }
  .services-text { position: absolute; left: 63px; top: 932px; font-size: 34px; font-weight: 700; color: var(--white); }

  .contact { position: absolute; left: 62px; list-style: none; }
  .contact li { display: flex; align-items: center; gap: 8px; font-weight: 600; }
  .contact .address { font-size: 25px; height: 38px; }
  .contact .phone { font-size: 31px; line-height: 40px; align-items: flex-start; }
  .contact .phone svg { margin-top: 6px; }
  .contact .email { font-size: 30px; height: 42px; }

  .social { position: absolute; left: 582px; top: 1074px; display: flex; align-items: center; gap: 16px; }
  .social-square { width: 58px; height: 58px; background: var(--brand-blue); }
  .social-lead { font-size: 22px; font-weight: 700; line-height: 1; }
  .social-name { font-size: 30px; font-weight: 700; line-height: 1.1; white-space: nowrap; }

  .accept { position: absolute; left: 835px; top: 950px; width: 320px; text-align: center; }
  .accept-title { font-size: 22px; font-weight: 500; letter-spacing: 9px; }
  .insurer { margin-top: 14px; font-size: 24px; font-weight: 800; color: var(--brand-green); line-height: 1; white-space: nowrap; }
  .cards { position: absolute; left: 850px; top: 1074px; width: 300px; height: 56px; display: flex; align-items: center; justify-content: space-between; }
  .partner-badge { width: 50px; height: 50px; border-radius: 50%; background: var(--brand-green); flex: none; }
  .card-name { font-size: 24px; font-weight: 800; white-space: nowrap; }
</style>
</head>
<body>
<main class="ad">

  <span class="brand-mark"></span>
  <div class="brand-text">
    <span class="brand-name">Cedarline Care</span>
    <span class="brand-sub">PHARMACY</span>
  </div>

  <div class="hours">
    <div class="hours-title">OPENING HOURS:</div>
    <div class="hours-line">Mon - Sat</div>
    <div class="hours-line">8:30am - 7pm</div>
    <div class="hours-line">Sun - 10am-2pm</div>
  </div>

  <div class="tagline">“Where Good Health Begins”</div>

  <div class="photo" role="img" aria-label="Photo of a smiling pharmacist in a white coat advising a customer at the pharmacy counter, shelves of products behind"></div>

  <svg class="feature-panel" width="1200" height="720" viewBox="0 0 1200 720" aria-hidden="true">
    <polygon points="612,312 1200,312 1200,719 505,719" fill="var(--brand-blue)"/>
  </svg>

  <ul class="features">
    <li><svg width="30" height="28" viewBox="0 0 30 28"><path d="M2 15 L11 25 L28 3" fill="none" stroke="var(--brand-green)" stroke-width="5" stroke-linecap="round" stroke-linejoin="round"/></svg>Certified Pharmacists</li>
    <li><svg width="30" height="28" viewBox="0 0 30 28"><path d="M2 15 L11 25 L28 3" fill="none" stroke="var(--brand-green)" stroke-width="5" stroke-linecap="round" stroke-linejoin="round"/></svg>Affordable prices</li>
    <li><svg width="30" height="28" viewBox="0 0 30 28"><path d="M2 15 L11 25 L28 3" fill="none" stroke="var(--brand-green)" stroke-width="5" stroke-linecap="round" stroke-linejoin="round"/></svg>Brand and Generic Medicines</li>
    <li><svg width="30" height="28" viewBox="0 0 30 28"><path d="M2 15 L11 25 L28 3" fill="none" stroke="var(--brand-green)" stroke-width="5" stroke-linecap="round" stroke-linejoin="round"/></svg>Blood Pressure and<br>Glucose checks</li>
    <li><svg width="30" height="28" viewBox="0 0 30 28"><path d="M2 15 L11 25 L28 3" fill="none" stroke="var(--brand-green)" stroke-width="5" stroke-linecap="round" stroke-linejoin="round"/></svg>Personal care and Beauty<br>Products</li>
    <li><svg width="30" height="28" viewBox="0 0 30 28"><path d="M2 15 L11 25 L28 3" fill="none" stroke="var(--brand-green)" stroke-width="5" stroke-linecap="round" stroke-linejoin="round"/></svg>Injectables</li>
  </ul>

  <section class="offer-band">
    <div class="offer offer-senior">
      <span class="offer-value" style="left:14px; top:28px;">10%</span>
      <span class="offer-label" style="left:305px; top:36px;">SENIOR<br>CITIZEN<br>DISCOUNT</span>
    </div>
    <div class="offer offer-student">
      <span class="offer-value" style="left:22px; top:14px;">10%</span>
      <span class="offer-label" style="left:311px; top:45px;">STUDENT<br>DISCOUNT</span>
      <span class="offer-note">With valid ID card</span>
    </div>
  </section>

  <svg class="services" width="820" height="60" viewBox="0 0 820 60" aria-hidden="true">
    <polygon points="0,0 815,0 800,60 0,60" fill="var(--brand-blue)"/>
  </svg>
  <div class="services-text">SPECIAL ORDERS | DELIVERY SERVICE</div>

  <ul class="contact" style="top:987px;">
    <li class="address">
      <svg width="32" height="32" viewBox="0 0 32 32"><circle cx="16" cy="16" r="14" fill="none" stroke="var(--brand-green)" stroke-width="2.5"/><path d="M8 16 L16 9 L24 16 M11 14 V23 H21 V14" fill="none" stroke="var(--brand-green)" stroke-width="2.5" stroke-linejoin="round"/></svg>
      Unit B4, Harbourview Plaza, Marine Road, Port Selden
    </li>
    <li class="phone">
      <svg width="32" height="32" viewBox="0 0 32 32"><circle cx="16" cy="16" r="14" fill="none" stroke="var(--brand-green)" stroke-width="2.5"/><path d="M11 8 L14 8 L15 12 L13 14 Q15 18 18 19 L20 17 L24 18 L24 21 Q22 24 18 22 Q11 19 9 12 Q9 9 11 8 Z" fill="none" stroke="var(--brand-green)" stroke-width="2" stroke-linejoin="round"/></svg>
      <span>1 555 310 4820 / 1 555 310 4821<br>1 555 310 4822</span>
    </li>
    <li class="email">
      <svg width="32" height="32" viewBox="0 0 32 32"><circle cx="16" cy="16" r="14" fill="none" stroke="var(--brand-green)" stroke-width="2.5"/><rect x="9" y="11" width="14" height="10" fill="none" stroke="var(--brand-green)" stroke-width="2"/><path d="M9 11 L16 17 L23 11" fill="none" stroke="var(--brand-green)" stroke-width="2"/></svg>
      cedarlinecare@mailbox.com
    </li>
  </ul>

  <div class="social">
    <span class="social-square"></span>
    <div>
      <div class="social-lead">Visit us on:</div>
      <div class="social-name">Friendbook</div>
    </div>
  </div>

  <div class="accept">
    <div class="accept-title">WE ACCEPT</div>
    <div class="insurer">Northway Insurances</div>
  </div>

  <div class="cards">
    <span class="partner-badge"></span>
    <span class="card-name">Cardline</span>
    <span class="card-name">Paynova</span>
  </div>

</main>
</body>
</html>
```